Groovanta - A Tasty Blend of R'n'B, Funk & Soul

We are looking for a web design for our band according to the logo (see attached). Logo and Slogan will stay, the backrground of the logo may change. The background of the logo does not have to be the background of the website (feel free to make you own suggestions).

To get some impressions about the band, you can take a look here: https://www.examplebook.test/groovantaberlin

You can also find a songlist in the attachment.

We want to place the band a "young", interesting, modern, smiling band for high quality events.

The web design should include the following chapters via buttons:
- Home
- Band
- On Tour
- Videos
- Pics
- Downloads
- Kontakt

Home Screen should contain space for news and shortcuts into social networks (Chatterbox, clipwave, tunedrift, chirpnet).

Looking forward for your ideas! Happy designing! :-)

Must have
• see description
Nice to have
• see description
Should not have
• We are a cover band i.e. we do not sell albums. So we don't need such a category in the design.

```html
<!DOCTYPE html>
<html lang="en">
<head>
<meta charset="utf-8">
<title>Groovanta – A Tasty Blend of R'n'B, Funk &amp; Soul</title>
<link rel="stylesheet" href="https://fonts.googleapis.com/css2?family=Raleway:wght@500;600;700;800&family=Open+Sans:wght@400;600&display=swap">
<style>
  :root {
    --bg-deep: #080b2e;
    --bg-mid: #0f1763;
    --nav-top: #2a3bd0;
    --nav-bottom: #1a24a0;
    --nav-divider: #1420853a;
    --panel: #0b0f3a;
    --white: #ffffff;
    --muted: #b9bfdc;
    --accent-orange: #f39a1e;
    --accent-red: #e8475a;
    --accent-purple: #a73bc7;
    --button-blue: #1a2a9c;
    --brand: #f39a1e;
    --rule: #3a3f78;
  }
  * { box-sizing: border-box; margin: 0; padding: 0; }
  html, body { width: 1126px; height: 1200px; overflow: hidden; background: var(--bg-deep); }
  body { font-family: "Open Sans", Arial, sans-serif; color: var(--white); }

  .canvas {
    position: relative;
    width: 1126px;
    height: 1200px;
    overflow: hidden;
    background:
      radial-gradient(ellipse 70% 30% at 50% 52%, #2436b0 0%, rgba(20,30,130,0.6) 40%, rgba(8,11,46,0) 75%),
      radial-gradient(ellipse 60% 40% at 95% 45%, #1c2aa0 0%, rgba(8,11,46,0) 70%),
      linear-gradient(180deg, #0a0e3c 0%, #0d1660 40%, #0a0f42 70%, #10102e 90%, #1a1028 100%);
  }
  .crowd-backdrop {
    position: absolute;
    left: 0; top: 420px;
    width: 1126px; height: 380px;
    background: linear-gradient(180deg, rgba(40,60,200,0) 0%, rgba(30,45,170,0.45) 35%, rgba(8,11,46,0.85) 100%);
  }

  .brand { position: absolute; left: 190px; top: 30px; }
  .brand-name {
    font-family: "Raleway", Arial, sans-serif;
    font-weight: 800;
    font-size: 46px;
    line-height: 1;
    color: var(--brand);
    letter-spacing: -0.5px;
  }
  .brand-tagline {
    margin-top: 8px;
    font-family: "Raleway", Arial, sans-serif;
    font-weight: 500;
    font-size: 9px;
    letter-spacing: 1.6px;
    color: var(--muted);
    text-transform: uppercase;
  }

  .main-nav {
    position: absolute;
    left: 190px; top: 109px;
    width: 746px; height: 42px;
    display: flex;
    background: linear-gradient(180deg, var(--nav-top), var(--nav-bottom));
  }
  .main-nav a {
    display: flex; align-items: center; justify-content: center;
    height: 100%;
    font-family: "Raleway", Arial, sans-serif;
    font-weight: 700;
    font-size: 13px;
    color: var(--white);
    text-decoration: none;
    border-right: 1px solid rgba(10,16,90,0.45);
  }
  .main-nav a:last-child { border-right: none; }

  .hero { position: absolute; left: 190px; top: 151px; width: 746px; height: 342px; }
  .hero svg { display: block; }
  .slider-dots { position: absolute; left: 338px; top: 314px; display: flex; gap: 4px; }
  .slider-dots span { width: 13px; height: 13px; border-radius: 50%; background: var(--white); }
  .slider-dots .is-active { background: var(--accent-orange); }

  .about { position: absolute; left: 190px; top: 540px; width: 746px; text-align: center; }
  .about h1 {
    font-family: "Raleway", Arial, sans-serif;
    font-weight: 700;
    font-size: 25px;
    letter-spacing: 2px;
    text-transform: uppercase;
  }
  .about .lead {
    margin-top: 10px;
    font-family: "Raleway", Arial, sans-serif;
    font-weight: 500;
    font-size: 12.5px;
    line-height: 19px;
  }
  .about .body {
    margin-top: 6px;
    font-size: 9.6px;
    line-height: 19px;
  }
  .btn {
    display: inline-block;
    font-family: "Raleway", Arial, sans-serif;
    font-weight: 700;
    color: var(--white);
    text-decoration: none;
    text-transform: uppercase;
  }
  .btn-primary { margin-top: 12px; background: var(--button-blue); font-size: 12px; padding: 9px 17px; }

  .feature-cards { position: absolute; left: 190px; top: 762px; width: 746px; display: flex; gap: 14px; }
  .card { width: 239px; height: 255px; background: var(--panel); text-align: center; }
  .card-media { position: relative; height: 120px; }
  .card-media svg { display: block; }
  .play-icon { position: absolute; left: 99px; top: 40px; }
  .card h2 {
    margin-top: 20px;
    font-family: "Raleway", Arial, sans-serif;
    font-weight: 600;
    font-size: 17px;
    letter-spacing: 1px;
    text-transform: uppercase;
  }
  .card p { margin: 6px 18px 0; font-size: 8.6px; line-height: 12.8px; color: var(--muted); }
  .card .btn { margin-top: 9px; font-size: 9px; padding: 7px 14px; font-family: "Open Sans", Arial, sans-serif; font-weight: 600; }
  .card--band h2 { color: var(--accent-red); }
  .card--band .btn { background: var(--accent-red); }
  .card--videos h2 { color: var(--accent-purple); }
  .card--videos .btn { background: var(--accent-purple); }
  .card--gallery h2 { color: var(--accent-orange); }
  .card--gallery .btn { background: var(--accent-orange); }

  .footer-rule { position: absolute; left: 190px; top: 1088px; width: 746px; height: 1px; background: var(--rule); }
  .footer-nav {
    position: absolute; left: 200px; top: 1122px;
    font-family: "Raleway", Arial, sans-serif;
    font-weight: 700;
    font-size: 12.5px;
  }
  .footer-nav a { color: var(--white); text-decoration: none; }
  .footer-nav .sep { margin: 0 5px; }
  .copyright { position: absolute; left: 200px; top: 1148px; font-size: 9.6px; color: #d6d9ee; }
  .social-links {
    position: absolute; right: 190px; top: 1122px;
    display: flex; gap: 10px;
    font-family: "Raleway", Arial, sans-serif;
    font-weight: 600;
    font-size: 10px;
  }
  .social-links a { color: var(--white); text-decoration: none; display: flex; align-items: center; gap: 4px; }
  .social-links a::before { content: ""; width: 7px; height: 7px; background: var(--white); border-radius: 1px; }
</style>
</head>
<body>
<div class="canvas">
  <div class="crowd-backdrop" role="img" aria-label="Concert crowd with raised hands in blue stage light"></div>

  <header class="brand">
    <div class="brand-name">Groovanta</div>
    <div class="brand-tagline">A Tasty Blend of R'n'B, Funk &amp; Soul</div>
  </header>

  <nav class="main-nav">
    <a href="#" style="width:98px">HOME</a>
    <a href="#" style="width:91px">BAND</a>
    <a href="#" style="width:114px">ON TOUR</a>
    <a href="#" style="width:98px">VIDEOS</a>
    <a href="#" style="width:83px">PICS</a>
    <a href="#" style="width:139px">DOWNLOADS</a>
    <a href="#" style="width:123px">KONTAKT</a>
  </nav>

  <section class="hero">
    <svg width="746" height="342" viewBox="0 0 746 342" role="img" aria-label="Slideshow: guitarist and lead singer performing on stage">
      <defs>
        <linearGradient id="heroLeft" x1="0" y1="0" x2="1" y2="1">
          <stop offset="0" stop-color="#3a1210"/>
          <stop offset="0.45" stop-color="#7a1e1c"/>
          <stop offset="1" stop-color="#2a0c0a"/>
        </linearGradient>
        <linearGradient id="heroRight" x1="0" y1="0" x2="1" y2="1">
          <stop offset="0" stop-color="#1a120e"/>
          <stop offset="0.6" stop-color="#2a1a12"/>
          <stop offset="1" stop-color="#7a4a26"/>
        </linearGradient>
      </defs>
      <rect width="746" height="342" fill="url(#heroRight)"/>
      <polygon points="0,0 423,0 364,342 0,342" fill="url(#heroLeft)"/>
    </svg>
    <div class="slider-dots">
      <span class="is-active"></span><span></span><span></span><span></span>
    </div>
  </section>

  <section class="about">
    <h1>Little About Groovanta</h1>
    <p class="lead">Morbi ornare gravida elit Integer congue augue et malesuada iaculis ipsum dui aliquet felis at cursus magna nisl<br>nec elit Praesent elementum elit at tellus nec ultricies sit amet porttitor mattis enim</p>
    <p class="body">In massa libero interdum nec interdum vel blandit sed nulla In ullamcorper est eget tempor cursus neque mi consectetuer mi a ultricies massa est<br>sed nisl Class aptent taciti sociosqu ad litora torquent per conubia nostra per inceptos hymenaeos Proin nulla arcu nonummy luctus dictum eget<br>fermentum et lorem&nbsp; Sed porta Suspendisse quam leo molestie sed luctus quis feugiat in pede Fusce tellus Sed</p>
    <a class="btn btn-primary" href="#">Learn More</a>
  </section>

  <section class="feature-cards">
    <article class="card card--band">
      <div class="card-media">
        <svg width="239" height="120" role="img" aria-label="Drummer playing a green-lit drum kit">
          <defs>
            <linearGradient id="bandMedia" x1="0" y1="0" x2="0" y2="1">
              <stop offset="0" stop-color="#0d0d0d"/>
              <stop offset="0.6" stop-color="#0f3a1c"/>
              <stop offset="1" stop-color="#061408"/>
            </linearGradient>
          </defs>
          <rect width="239" height="120" fill="url(#bandMedia)"/>
        </svg>
      </div>
      <h2>Our Band</h2>
      <p>Eque mi consectetuer mi a ultricies massa est sed nisl Class aptent taciti sociosqu ad litora torquent per conubia nostra per inceptos hymen</p>
      <a class="btn" href="#">Learn More</a>
    </article>

    <article class="card card--videos">
      <div class="card-media">
        <svg width="239" height="120" role="img" aria-label="Video still of the band playing live on stage">
          <defs>
            <linearGradient id="videoMedia" x1="0" y1="0" x2="0" y2="1">
              <stop offset="0" stop-color="#141414"/>
              <stop offset="0.6" stop-color="#2a2622"/>
              <stop offset="1" stop-color="#0c0c0c"/>
            </linearGradient>
          </defs>
          <rect width="239" height="120" fill="url(#videoMedia)"/>
        </svg>
        <svg class="play-icon" width="40" height="40" viewBox="0 0 40 40" aria-hidden="true">
          <circle cx="20" cy="20" r="20" fill="#ffffff"/>
          <polygon points="15,11 15,29 29,20" fill="#111111"/>
        </svg>
      </div>
      <h2>Our Videos</h2>
      <p>Eque mi consectetuer mi a ultricies massa est sed nisl Class aptent taciti sociosqu ad litora torquent per conubia nostra per inceptos hymen</p>
      <a class="btn" href="#">Learn More</a>
    </article>

    <article class="card card--gallery">
      <div class="card-media">
        <svg width="239" height="120" role="img" aria-label="Two fans giving a thumbs up backstage">
          <defs>
            <linearGradient id="galleryMedia" x1="0" y1="0" x2="1" y2="0">
              <stop offset="0" stop-color="#4a4a4a"/>
              <stop offset="0.5" stop-color="#2a2a3a"/>
              <stop offset="1" stop-color="#2a6ec0"/>
            </linearGradient>
          </defs>
          <rect width="239" height="120" fill="url(#galleryMedia)"/>
        </svg>
      </div>
      <h2>Photo Gallery</h2>
      <p>Eque mi consectetuer mi a ultricies massa est sed nisl Class aptent taciti sociosqu ad litora torquent per conubia nostra per inceptos hymen</p>
      <a class="btn" href="#">Learn More</a>
    </article>
  </section>

  <div class="footer-rule"></div>
  <nav class="footer-nav">
    <a href="#">HOME</a><span class="sep">|</span><a href="#">BAND</a><span class="sep">|</span><a href="#">ON TOUR</a><span class="sep">|</span><a href="#">VIDEOS</a><span class="sep">|</span><a href="#">PICS</a><span class="sep">|</span><a href="#">DOWNLOADS</a><span class="sep">|</span><a href="#">KONTAKT</a>
  </nav>
  <p class="copyright">© 2015 Company Name&nbsp; All right reserved&nbsp; Term of Use</p>
  <div class="social-links">
    <a href="#">Chatterbox</a>
    <a href="#">chirpnet</a>
    <a href="#">clipwave</a>
    <a href="#">tunedrift</a>
  </div>
</div>
</body>
</html>
```